Quarrybend Marble & Tile Needs a Business Card

Attached you will find your logo, my photo and design guidelines for a new business card. The final design will need two separate files to create an embossed card. The cards will be printed by www.plinkprint.com (Instructions below)
Format is the Plink SQUARE card
Quarrybend Marble And Tile is a brick and mortar, retail stone and tile shop.
One the front:
Quarrybend Marble And Tile
Dorian Fesslock
Owner
24807 Hollis Verdant Blvd
Suite P & R
Charlotte, NC 28193
Cell: 704-583-7142
Web: www.QuarrybendMarbleAndTile.com
(Make each word of the domain a different or alternating color)
On the back;
Something that shows beautiful colorful tile
Follow the design guide closely please. For more information see this page that describes creating the spot gloss file: https://www.plinkprint.com/us/business-cards/design-guidelines-spot-gloss
The logo is what we would like to have raised spot glossed.
Format is the Plink SQUARE card. See attahced guidlines.

```html
<!DOCTYPE html>
<html lang="en">
<head>
<meta charset="utf-8">
<title>Quarrybend Marble &amp; Tile — Business Card</title>
<link rel="stylesheet" href="https://fonts.googleapis.com/css2?family=Cinzel:wght@500&family=Playfair+Display:wght@800&family=Poppins:wght@400;500&display=swap">
<style>
  :root {
    --rust: #a5432a;
    --navy: #1f2e3a;
    --gold: #b07a2a;
    --paper: #ffffff;
    --backdrop: #e4e4e4;
    --ink: #26313a;
    --tile-soft-a: #f3e6df;
    --tile-soft-b: #e7eaee;
  }
  * { box-sizing: border-box; margin: 0; padding: 0; }
  html, body { width: 1200px; height: 1049px; overflow: hidden; }
  body {
    background: var(--backdrop);
    position: relative;
    font-family: "Poppins", sans-serif;
  }
  .card {
    position: absolute;
    left: 180px;
    width: 840px;
    height: 480px;
    overflow: hidden;
  }
  /* Back side */
  .card-back { top: 30px; background: var(--rust); }
  .back-tile-field {
    position: absolute;
    right: -60px; bottom: -80px;
    width: 460px; height: 420px;
    background: radial-gradient(circle at 50% 50%, rgba(255,255,255,0.09), rgba(255,255,255,0.03) 60%, rgba(255,255,255,0) 72%);
  }
  .back-brand {
    position: absolute;
    left: 150px; top: 170px;
    display: flex; align-items: center; gap: 28px;
  }
  .brand-square {
    width: 34px; height: 34px;
    background: #ffffff;
  }
  .back-brand .brand-name {
    font-family: "Cinzel", serif;
    font-weight: 500;
    color: #ffffff;
    line-height: 1.15;
  }
  .brand-name .line-main { display: block; font-size: 64px; letter-spacing: 6px; }
  .brand-name .line-sub { display: block; font-size: 24px; letter-spacing: 12px; margin-top: 6px; }

  /* Front side */
  .card-front { top: 540px; background: var(--paper); }
  .front-tile-field {
    position: absolute;
    left: 520px; top: -20px;
    width: 340px; height: 500px;
    background: radial-gradient(circle at 55% 45%, var(--tile-soft-a) 0%, var(--tile-soft-b) 45%, rgba(255,255,255,0) 72%);
  }
  .portrait {
    position: absolute;
    left: 580px; top: 70px;
    width: 210px; height: 245px;
    background: linear-gradient(180deg, #c9a58c 0%, #a77d64 45%, #2c3a4d 75%, #24314a 100%);
  }
  .front-brand {
    position: absolute;
    left: 60px; top: 78px;
    display: flex; align-items: center; gap: 22px;
  }
  .front-brand .brand-square { background: var(--rust); width: 30px; height: 30px; }
  .front-brand .brand-name { font-family: "Cinzel", serif; font-weight: 500; color: var(--navy); line-height: 1.15; }
  .front-brand .line-main { font-size: 50px; letter-spacing: 5px; }
  .front-brand .line-sub { font-size: 19px; letter-spacing: 9px; }

  .holder { position: absolute; left: 62px; top: 218px; }
  .holder-name {
    font-family: "Playfair Display", serif;
    font-weight: 800;
    font-size: 38px;
    color: var(--rust);
    letter-spacing: 1px;
  }
  .holder-title {
    font-family: "Playfair Display", serif;
    font-weight: 800;
    font-size: 24px;
    color: var(--gold);
    letter-spacing: 1px;
    margin-top: 2px;
  }
  .divider { position: absolute; left: 0; top: 310px; width: 840px; height: 30px; }

  .contacts {
    position: absolute;
    left: 62px; top: 352px;
    font-size: 17px;
    color: var(--ink);
  }
  .contact-row { display: flex; align-items: center; gap: 10px; height: 34px; }
  .contact-row + .contact-row { margin-left: 0; }
  .contact-group { display: flex; gap: 34px; }
  .contact-rule { width: 560px; height: 1px; background: var(--gold); margin: 8px 0; }
  .icon { width: 16px; height: 16px; flex: none; }
  .web .w1 { color: var(--ink); }
  .web .w2 { color: var(--rust); }
  .web .w3 { color: var(--gold); }
  .web .w4 { color: var(--navy); }
</style>
</head>
<body>

<section class="card card-back" aria-label="Card back">
  <div class="back-tile-field" role="img" aria-label="Faint geometric tile pattern"></div>
  <div class="back-brand">
    <span class="brand-square"></span>
    <div class="brand-name">
      <span class="line-main">QUARRYBEND</span>
      <span class="line-sub">MARBLE &amp; TILE</span>
    </div>
  </div>
</section>

<section class="card card-front" aria-label="Card front">
  <div class="front-tile-field" role="img" aria-label="Soft colourful mosaic tile pattern"></div>
  <div class="portrait" role="img" aria-label="Portrait photo of Dorian Fesslock"></div>

  <div class="front-brand">
    <span class="brand-square"></span>
    <div class="brand-name">
      <span class="line-main">QUARRYBEND</span>
      <span class="line-sub">MARBLE &amp; TILE</span>
    </div>
  </div>

  <div class="holder">
    <div class="holder-name">DORIAN FESSLOCK</div>
    <div class="holder-title">OWNER</div>
  </div>

  <svg class="divider" viewBox="0 0 840 30" aria-hidden="true">
    <polygon points="40,6 440,6 426,24 40,24" fill="var(--navy)"/>
    <line x1="440" y1="6" x2="810" y2="6" stroke="var(--gold)" stroke-width="4"/>
  </svg>

  <div class="contacts">
    <div class="contact-group">
      <div class="contact-row">
        <svg class="icon" viewBox="0 0 16 16" aria-hidden="true"><rect x="4" y="1" width="8" height="14" rx="1.5" fill="none" stroke="var(--rust)" stroke-width="1.5"/><line x1="7" y1="12.5" x2="9" y2="12.5" stroke="var(--rust)" stroke-width="1.2"/></svg>
        <span>704-583-7142</span>
      </div>
      <div class="contact-row web">
        <svg class="icon" viewBox="0 0 16 16" aria-hidden="true"><circle cx="8" cy="8" r="6.5" fill="none" stroke="var(--rust)" stroke-width="1.4"/><ellipse cx="8" cy="8" rx="2.8" ry="6.5" fill="none" stroke="var(--rust)" stroke-width="1.1"/><line x1="1.5" y1="8" x2="14.5" y2="8" stroke="var(--rust)" stroke-width="1.1"/></svg>
        <span><span class="w1">www.</span><span class="w2">Quarrybend</span><span class="w3">Marble</span><span class="w4">And</span><span class="w2">Tile</span><span class="w1">.com</span></span>
      </div>
    </div>
    <div class="contact-rule"></div>
    <div class="contact-row">
      <svg class="icon" viewBox="0 0 16 16" aria-hidden="true"><path d="M8 1a5 5 0 0 0-5 5c0 3.6 5 9 5 9s5-5.4 5-9a5 5 0 0 0-5-5z" fill="var(--rust)"/><circle cx="8" cy="6" r="1.8" fill="#fff"/></svg>
      <span>24807 Hollis Verdant Blvd Suite P &amp; R Charlotte, NC 28193</span>
    </div>
  </div>
</section>

</body>
</html>
```